Modern Medical Optometry Website

We need mordern, Patient friendly website. Easy to navigate and enhance our advance medical technology and excellent patient care.
1. HOME PAGE
2. OUR TEAM PAGE
3. EYECARE PAGE - VISION SERVICES, EYE EXAMS, KERATOCONUS CENTER, GLAUCOMA , DIABITES, MELORIDEX EXAM, DIGITAL RETINAL, OCT.
4. MYOPIA CONTROL CLINIC
5. DRY EYE CLINIC
6. EYEWEAR
7. PATIENT CENTER - BLOG
7. CONTACT US
This is our current website www.brivaloka.com
and We want to add more content and a cleaner design like these website
http://tarnwickfolvendale.com/
https://www.qmvorlu.com/

```html
<!DOCTYPE html>
<html lang="en">
<head>
<meta charset="utf-8">
<title>Myopia Control Clinic – Vireo Optometry</title>
<link href="https://fonts.googleapis.com/css2?family=Montserrat:wght@300;400;500;600;700&display=swap" rel="stylesheet">
<style>
:root{
  --teal:#0d87a8;
  --teal-dark:#0b7795;
  --yellow:#fce660;
  --grey-band:#f2f2f2;
  --text:#444;
  --muted:#8a8a8a;
  --dark:#2b2b2b;
  --white:#fff;
}
*{box-sizing:border-box;margin:0;padding:0}
html,body{width:1200px;height:3604px;overflow:hidden}
body{position:relative;background:var(--white);font-family:"Montserrat",sans-serif;color:var(--text)}
.abs{position:absolute}
/* top bar */
.topbar{left:0;top:0;width:1200px;height:52px;background:var(--teal)}
.topbar .item{position:absolute;top:0;height:52px;display:flex;align-items:center;gap:10px;color:var(--white);font-size:14px;font-weight:500;border-left:1px solid rgba(255,255,255,.25);padding:0 20px}
.topbar .social{position:absolute;top:0;width:52px;height:52px;border-left:1px solid rgba(255,255,255,.25);display:flex;align-items:center;justify-content:center}
.topbar .social span{width:10px;height:10px;border-radius:50%;background:var(--yellow)}
/* brand */
.brand{left:77px;top:21px;width:109px;height:144px;background:var(--white);display:flex;flex-direction:column;align-items:center;justify-content:center;gap:10px}
.brand .mark{width:40px;height:40px;background:var(--yellow)}
.brand .name{font-size:13px;font-weight:500;color:#777;text-align:center;line-height:1.2}
.nav{left:220px;top:110px;display:flex;gap:36px;font-size:16px;color:#888;font-weight:400}
.nav .active{color:var(--teal)}
.nav .home{color:#666;font-weight:500}
.search{left:1102px;top:108px}
/* title band */
.title-band{left:0;top:187px;width:1200px;height:136px;background:var(--grey-band);display:flex;align-items:center;justify-content:center}
.title-band h1{color:var(--teal);font-size:36px;font-weight:600}
/* intro */
.intro{left:79px;top:362px;width:1040px}
.intro h2{font-size:35px;font-weight:400;color:var(--dark);margin-bottom:40px}
.intro p{font-size:13.2px;line-height:26px;color:var(--muted);margin-bottom:26px}
.intro strong{color:#111;font-weight:600}
/* feature grid */
.photo{background:linear-gradient(135deg,#e9eef1,#d8cfc6 45%,#f6f6f6)}
.photo-child{background:linear-gradient(135deg,#f3f1ec,#e8d9c8 50%,#f5e3e6)}
.tile{padding:0 42px}
.tile h3{font-size:29px;font-weight:600;margin-bottom:14px}
.tile p{font-size:13.3px;line-height:26px}
.tile.teal{background:var(--teal);color:var(--white)}
.tile.yellow{background:var(--yellow);color:#333}
/* old band */
.old{left:0;top:1792px;width:1200px;height:259px;background:var(--yellow);padding:50px 79px 0}
.old h3{font-size:29px;font-weight:600;color:#333;margin-bottom:12px}
.old p{font-size:13.3px;line-height:26px;color:#444;width:1040px}
.next{left:79px;top:2094px;width:1000px}
.next h3{font-size:29px;font-weight:600;color:#333;margin-bottom:12px}
.next p{font-size:13.3px;line-height:26px;color:#444}
.more-title{left:0;top:2276px;width:1303px;text-align:center;font-size:30px;font-weight:600;color:var(--teal)}
.links{left:77px;top:2347px;width:1047px;height:103px;display:flex}
.links a{flex:1;display:flex;align-items:center;justify-content:center;font-size:30px;text-decoration:none;color:var(--white);background:var(--teal);font-weight:400}
.links a.alt{background:var(--yellow);color:#333}
/* testimonials */
.testi-title{left:0;top:2510px;width:1200px;text-align:center;font-size:36px;font-weight:600;color:var(--teal)}
.video{top:2592px;width:234px;height:240px;background:linear-gradient(160deg,#f2cc1e,#e9d9a8 55%,#cfcfcf);display:flex;align-items:center;justify-content:center}
.arrow{top:2683px;width:47px;height:47px;display:flex;align-items:center;justify-content:center}
.arrow.left{left:19px;background:var(--yellow)}
.arrow.right{left:1134px;background:var(--teal)}
/* brands */
.brands{left:94px;top:2895px;width:1030px;display:flex;justify-content:space-between;font-size:24px;font-weight:700;color:#222}
.brands span{width:150px;text-align:center}
.frames{left:94px;top:2988px;width:1030px;display:flex;justify-content:space-between}
.frames div{width:126px;height:56px;border-radius:28px;background:linear-gradient(90deg,#c9c9c9,#eee 50%,#c9c9c9)}
/* footer */
.footer{left:0;top:3125px;width:1200px;height:410px;background:var(--yellow)}
.fcol{position:absolute;top:60px}
.fcol h4{font-size:19px;font-weight:600;color:var(--teal);margin-bottom:24px}
.row{display:flex;gap:16px;font-size:13.5px;color:#444;line-height:26px;margin-bottom:16px;align-items:flex-start}
.row svg{flex:none;margin-top:4px}
.hours p{font-size:13.5px;line-height:31px;color:#444}
.hours b{font-weight:600;color:#222}
.dir{position:absolute;top:3440px;width:280px;height:40px;border-radius:20px;background:var(--dark);color:var(--white);font-size:14px;display:flex;align-items:center;padding:0 18px;gap:22px}
.fsocial{position:absolute;top:3440px;display:flex;gap:12px}
.fsocial span{width:40px;height:40px;border-radius:50%;background:var(--dark);display:flex;align-items:center;justify-content:center}
.fsocial span i{width:9px;height:9px;border-radius:50%;background:var(--yellow)}
.fsocial span.first{background:var(--teal)}
.copy{left:0;top:3557px;width:1200px;text-align:center;font-size:13px;color:#888}
.copy b{color:var(--teal);font-weight:600}
</style>
</head>
<body>

<header>
  <div class="abs topbar">
    <div class="item" style="left:464px">
      <svg width="20" height="20" viewBox="0 0 24 24" fill="none" stroke="#fce660" stroke-width="2"><path d="M22 16.9v3a2 2 0 0 1-2.2 2 19.8 19.8 0 0 1-8.6-3.1 19.5 19.5 0 0 1-6-6A19.8 19.8 0 0 1 2.1 4.2 2 2 0 0 1 4.1 2h3a2 2 0 0 1 2 1.7c.1 1 .4 1.9.7 2.8a2 2 0 0 1-.5 2.1L8 9.8a16 16 0 0 0 6 6l1.3-1.3a2 2 0 0 1 2.1-.4c.9.3 1.8.6 2.8.7a2 2 0 0 1 1.7 2z"/></svg>
      555-210-4830
    </div>
    <div class="item" style="left:634px">
      <svg width="20" height="16" viewBox="0 0 24 18" fill="none" stroke="#fce660" stroke-width="2"><rect x="1" y="1" width="22" height="16"/><path d="M1 1l11 9 11-9"/></svg>
      hello@vireooptics.com
    </div>
    <div class="social" style="left:915px"><span></span></div>
    <div class="social" style="left:967px"><span></span></div>
    <div class="social" style="left:1019px"><span></span></div>
    <div class="social" style="left:1071px;border-right:1px solid rgba(255,255,255,.25)"><span></span></div>
  </div>
  <div class="abs brand">
    <div class="mark"></div>
    <div class="name">Vireo<br>Optometry</div>
  </div>
  <nav class="abs nav">
    <span class="home">HOME</span><span>OUR TEAM</span><span>EYE CARE</span><span class="active">MYOPIA CONTROL CLINIC</span><span>EYEWEAR</span><span>BLOG</span><span>CONTACT US</span>
  </nav>
  <svg class="abs search" width="20" height="20" viewBox="0 0 24 24" fill="none" stroke="#0d87a8" stroke-width="2"><circle cx="10" cy="10" r="7"/><path d="M15 15l7 7"/></svg>
</header>

<section class="abs title-band"><h1>MYOPIA CONTROL CLINIC</h1></section>

<section class="abs intro">
  <h2>What is Orthokeratology (OrthoK)?</h2>
  <p>Dr. Morrow is excited to offer a nonsurgical procedure using specially designed contact lenses to gently reshape the curvature of the eye to improve vision while you sleep. It works each night while you sleep for eight hours. You put the lenses on when you go to bed and remove them when you wake up. Your vision is clear during the day, without glasses or daytime contact lenses. Now you can enjoy your days with clear vision at school, work, and playing sports without the hassle of glasses or contact lenses drying out your eyes during the day.</p>
  <p><strong>Understanding OrthoK</strong> Our eyes must be in focus for us to see clearly, just as a camera must be in focus to obtain a sharp photo. Light, which gives us vision, is focused largely by the eye's front surface or cornea. OrthoK gently molds or focuses the cornea while a person is sleeping, creating a sharpened image when they wake. Dr. Morrow will design the OrthoK mold to obtain the change needed to achieve clearly focused vision. When the lens is removed in the morning the cornea begins to return to its original shape but so slowly that good vision is maintained all waking hours. Each night the process is repeated although some find they only need to wear their molds every other night, depending on prescription. The elastic tissue of the eye is not harmed by this daily process. OrthoK is safe and reversible. It is not a permanent alteration of tissue and thus is an excellent Lasik alternative for those reluctant or unable to undergo a surgical alteration of their corneas.</p>
</section>

<div class="abs photo" style="left:0;top:825px;width:600px;height:530px" role="img" aria-label="Woman with focus frame over her eye beside an eye chart"></div>
<div class="abs tile teal" style="left:600px;top:825px;width:600px;height:218px;padding-top:42px">
  <h3>Who is a Candidate?</h3>
  <p>The majority of nearsighted (myopic) individuals with healthy eyes can benefit from OrthoK, from children as young as seven years to adults in their 50s.</p>
</div>
<div class="abs tile yellow" style="left:600px;top:1043px;width:600px;height:312px;padding-top:42px;padding-right:70px">
  <h3>Will My Prescription Work?</h3>
  <p>OrthoK treats myopia (nearsightedness), the condition where distance vision is blurred. Prescription powers up to about -7.00 are generally treatable. Astigmatism, a common optical condition where vision is distorted due to uneven curvatures of the eye surfaces, is treatable in low to moderate amounts. Some doctors using specialized OrthoK lenses routinely exceed these levels for many patients with great success.</p>
</div>
<div class="abs tile teal" style="left:0;top:1355px;width:600px;height:437px;padding:42px 40px 0 79px">
  <h3>Can my child have OrthoK?</h3>
  <p>Patients as young as seven years old are excellent candidates and we make the decision based on their maturity, hygiene and motivation. These students are able to play, swim, participate in sports and other healthy activities without the problems of glasses or daytime contact lens wear. Perhaps the most exciting candidate for OrthoK is the young patient who has become nearsighted for the first time when there is a strong family history of nearsightedness progressing rapidly during childhood. The child whose nearsightedness has been proven to already be progressing is another excellent candidate. There is growing evidence that OrthoK can stop this progression.</p>
</div>
<div class="abs photo-child" style="left:600px;top:1355px;width:600px;height:437px" role="img" aria-label="Smiling young girl wearing glasses at a table"></div>

<section class="abs old">
  <h3>Am I too old for OrthoK?</h3>
  <p>Probably not! Patients over forty years old will generally need to consider the fact that near reading vision may be blurred, the same thing that happens to everyone with good distance vision as they get older. This condition (presbyopia) can be treated by modifying the power of OrthoK lenses, wearing reading glasses or other options that can be discussed with your doctor. Many patients in their sixties and seventies are wearing OrthoK lenses successfully.</p>
</section>

<section class="abs next">
  <h3>What do I do next?</h3>
  <p>The next step is visit Vireo Optometry for a free consultation and we will let you know based on your prescription if you are a good candidate for OrthoK.</p>
</section>

<div class="abs more-title">For Additional Information Click Here:</div>
<div class="abs links">
  <a href="#">ClearNite Lens</a>
  <a href="#" class="alt">Sight Guide Hub</a>
  <a href="#">Learn More</a>
</div>

<div class="abs testi-title">TESTIMONIALS</div>
<div class="abs arrow left"><svg width="22" height="14" viewBox="0 0 22 14" fill="none" stroke="#333" stroke-width="1.6"><path d="M21 7H2M7 1L1 7l6 6"/></svg></div>
<div class="abs arrow right"><svg width="22" height="14" viewBox="0 0 22 14" fill="none" stroke="#fff" stroke-width="1.6"><path d="M1 7h19M15 1l6 6-6 6"/></svg></div>
<div class="abs video" style="left:76px" role="img" aria-label="Patient testimonial video one"><svg width="62" height="62" viewBox="0 0 62 62"><circle cx="31" cy="31" r="28" fill="none" stroke="#fff" stroke-width="4"/><path d="M24 18l20 13-20 13z" fill="#fff"/></svg></div>
<div class="abs video" style="left:347px" role="img" aria-label="Patient testimonial video two"><svg width="62" height="62" viewBox="0 0 62 62"><circle cx="31" cy="31" r="28" fill="none" stroke="#fff" stroke-width="4"/><path d="M24 18l20 13-20 13z" fill="#fff"/></svg></div>
<div class="abs video" style="left:618px" role="img" aria-label="Patient testimonial video three"><svg width="62" height="62" viewBox="0 0 62 62"><circle cx="31" cy="31" r="28" fill="none" stroke="#fff" stroke-width="4"/><path d="M24 18l20 13-20 13z" fill="#fff"/></svg></div>
<div class="abs video" style="left:888px" role="img" aria-label="Patient testimonial video four"><svg width="62" height="62" viewBox="0 0 62 62"><circle cx="31" cy="31" r="28" fill="none" stroke="#fff" stroke-width="4"/><path d="M24 18l20 13-20 13z" fill="#fff"/></svg></div>

<div class="abs brands"><span>ALDEN</span><span>VESPER ROW</span><span>MARLOW &amp; CO.</span><span>TORVANO</span><span>BELLANE</span><span>KESTREL</span></div>
<div class="abs frames">
  <div role="img" aria-label="Blue-lens sunglasses"></div>
  <div role="img" aria-label="Round tortoise frames"></div>
  <div role="img" aria-label="Round brown sunglasses"></div>
  <div role="img" aria-label="Thin gold frames"></div>
  <div role="img" aria-label="Black cat-eye frames"></div>
  <div role="img" aria-label="Light tinted sunglasses"></div>
</div>

<footer class="abs footer">
  <div class="fcol" style="left:79px">
    <h4>Vireo Optometry</h4>
    <div class="row"><svg width="22" height="18" viewBox="0 0 24 24" fill="#0d87a8"><path d="M6.6 10.8a15 15 0 0 0 6.6 6.6l2.2-2.2a1 1 0 0 1 1-.3c1.1.4 2.3.6 3.6.6a1 1 0 0 1 1 1V20a1 1 0 0 1-1 1A17 17 0 0 1 3 4a1 1 0 0 1 1-1h3.5a1 1 0 0 1 1 1c0 1.3.2 2.5.6 3.6a1 1 0 0 1-.3 1z"/></svg>555-210-4830</div>
    <div class="row"><svg width="22" height="18" viewBox="0 0 24 20" fill="#0d87a8"><rect x="3" y="0" width="14" height="6"/><rect x="0" y="7" width="24" height="11" rx="2"/></svg>555-210-4871</div>
    <div class="row"><svg width="22" height="16" viewBox="0 0 24 18" fill="#0d87a8"><path d="M0 0h24v2L12 10 0 2z"/><path d="M0 5l12 8 12-8v13H0z"/></svg>info@brivaloka.com</div>
    <div class="row"><svg width="22" height="20" viewBox="0 0 24 24" fill="#0d87a8"><path d="M12 0a8 8 0 0 0-8 8c0 6 8 16 8 16s8-10 8-16a8 8 0 0 0-8-8zm0 11a3 3 0 1 1 0-6 3 3 0 0 1 0 6z"/></svg>4410 Ashgrove Ave., Dellmont,<br>CA 90012</div>
  </div>
  <div class="fcol" style="left:435px">
    <h4>Northvale</h4>
    <div class="row"><svg width="22" height="18" viewBox="0 0 24 24" fill="#0d87a8"><path d="M6.6 10.8a15 15 0 0 0 6.6 6.6l2.2-2.2a1 1 0 0 1 1-.3c1.1.4 2.3.6 3.6.6a1 1 0 0 1 1 1V20a1 1 0 0 1-1 1A17 17 0 0 1 3 4a1 1 0 0 1 1-1h3.5a1 1 0 0 1 1 1c0 1.3.2 2.5.6 3.6a1 1 0 0 1-.3 1z"/></svg>555-318-6092</div>
    <div class="row"><svg width="22" height="16" viewBox="0 0 24 18" fill="#0d87a8"><path d="M0 0h24v2L12 10 0 2z"/><path d="M0 5l12 8 12-8v13H0z"/></svg>northvale@brivaloka.com</div>
    <div class="row"><svg width="22" height="20" viewBox="0 0 24 24" fill="#0d87a8"><path d="M12 0a8 8 0 0 0-8 8c0 6 8 16 8 16s8-10 8-16a8 8 0 0 0-8-8zm0 11a3 3 0 1 1 0-6 3 3 0 0 1 0 6z"/></svg>2287 Calloway St., Suite 4,<br>Northvale, CA 90018</div>
  </div>
  <div class="fcol hours" style="left:791px">
    <h4>Opening Hours</h4>
    <p>Monday - Thursday : <b>9 am - 6 pm</b></p>
    <p>Friday : <b>8.30 am - 5 pm</b></p>
    <p>Saturday &nbsp;: <b>8.30 am- 5 pm</b></p>
    <p>Closed on <b>Sundays</b></p>
    <p style="line-height:20px;margin-top:6px">Please keep in mind we are closed<br>for <b>lunch 1-2 pm</b></p>
  </div>
</footer>
<div class="dir" style="left:77px">Get directions on the map <svg width="30" height="10" viewBox="0 0 30 10" fill="none" stroke="#0d87a8" stroke-width="1.6"><path d="M0 5h28M24 1l4 4-4 4"/></svg></div>
<div class="dir" style="left:433px">Get directions on the map <svg width="30" height="10" viewBox="0 0 30 10" fill="none" stroke="#0d87a8" stroke-width="1.6"><path d="M0 5h28M24 1l4 4-4 4"/></svg></div>
<div class="fsocial" style="left:790px"><span class="first"><i></i></span><span><i></i></span><span><i></i></span><span><i></i></span></div>

<div class="abs copy">Copyright © <b>VIREO OPTOMETRY</b> - 2019 . All right Reserved</div>
</body>
</html>
```